Business Card (double-sided) and Stationary Design for dental office

1) Business Card Design: We need a business card design for a dental specialty office.
Texts should contain:
The name of our office "Brindle Oaks Orthodontics"
Tagline: "Specialist in Orthodontic and Maxillofacial Orthopedics"
Tag line: "Creating "Tolvering" smiles for Children and Adults"
Doctor name: "Doctor Name"
Office Address:
"123 Street Name
City, State Zip code"
Office email address: office@brindleoaksortho.com
Website: www.brindleoaksortho.com

We will provide the full office address once the design is selected
Theme: beach, paradise, coastal, wave
We would like to have some creativity in design. Some acceptable ideas: front page: logo and office name. Back page: more detail information, and map to office in form of an island. Please see sample from our other location, but you DON'T HAVE TO USE OR COPY THE SAME CONCEPT.

IF POSSIBLE, PLEASE SUBMIT AT LEAST TWO CONCEPTS: ONE WITH THE BACK LOOKING SIMILAR TO WHAT IS IN THE SAMPLE, AND ONE DIFFERENT.

Color: designer to choose. We have different shade of blues and sand color in our office. Please see logo.

2) Please also design a matching set of stationary that compliment the business card and our logo.

Target Market(s)

Dental

Contact Information for Business Card

See descriptions

Font styles to use
Other font styles liked:
• Matching texts in logo

Colors
0054AA
0677BA
7BADD7
CADEEF
E8F1F8
0094D4
00A9DD
6FCCEA
C7EBF8
E9F6FB
00AB8E
00BBA5
67D7C9
C6EFE9
E9F9F6

Requirements
Must have
• Double-sided
Nice to have
• Beach coastal theme
Should not have
• Any shape or drawing of of tooth or teeth. We don’t need these. You don't necessarily have to just cut and paste the logo art and text as a whole, you have the liberty to rearrange the text.

```html
<!DOCTYPE html>
<html lang="en">
<head>
<meta charset="utf-8">
<title>Brindle Oaks Orthodontics – Letterhead</title>
<link rel="stylesheet" href="https://fonts.googleapis.com/css2?family=Montserrat:wght@700&family=Open+Sans:wght@600&family=Roboto+Slab:wght@400&display=swap">
<style>
  :root {
    --ink: #111111;
    --brand-blue: #3a8fa8;
    --brand-mint: #80cfbd;
    --sea-deep: #31bba3;
    --sea-light: #72cfbf;
    --paper: #ffffff;
    --frame: #333333;
    --header-line: #e2e2e2;
  }
  html, body {
    margin: 0;
    padding: 0;
    width: 1100px;
    height: 1200px;
    overflow: hidden;
    background: var(--paper);
  }
  .letterhead {
    position: relative;
    width: 1100px;
    height: 1200px;
    background: var(--paper);
    overflow: hidden;
  }
  .letterhead__art {
    position: absolute;
    inset: 0;
    width: 1100px;
    height: 1200px;
  }
  .brand {
    position: absolute;
    left: 65px;
    top: 56px;
    display: flex;
    flex-direction: column;
    align-items: flex-start;
  }
  .brand__dot {
    width: 96px;
    height: 96px;
    border-radius: 50%;
    background: var(--brand-blue);
    margin-left: 84px;
    margin-bottom: 16px;
  }
  .brand__name {
    font-family: "Open Sans", sans-serif;
    font-weight: 600;
    font-size: 27px;
    letter-spacing: 0.5px;
    color: var(--brand-blue);
    margin: 0;
    line-height: 1;
  }
  .contact {
    position: absolute;
    right: 66px;
    top: 72px;
    text-align: right;
    color: var(--ink);
  }
  .contact__doctor {
    font-family: "Montserrat", sans-serif;
    font-weight: 700;
    font-size: 14.5px;
    margin: 0 0 12px;
    letter-spacing: 0.2px;
  }
  .contact__line {
    font-family: "Roboto Slab", serif;
    font-size: 16.5px;
    margin: 0;
    line-height: 26.5px;
  }
</style>
</head>
<body>
  <main class="letterhead">
    <svg class="letterhead__art" viewBox="0 0 1848 2016" width="1100" height="1200" aria-hidden="false">
      <defs>
        <linearGradient id="header-shadow" x1="0" y1="0" x2="0" y2="1">
          <stop offset="0" stop-color="#d8d8d8"/>
          <stop offset="1" stop-color="#ffffff" stop-opacity="0"/>
        </linearGradient>
      </defs>
      <rect class="header-shadow" x="26" y="513" width="1796" height="6" fill="url(#header-shadow)"/>
      <line class="header-divider" x1="26" y1="513" x2="1822" y2="513" stroke="var(--header-line)" stroke-width="1.5"/>

      <rect class="illustration illustration--left" x="0" y="495" width="460" height="495" rx="180" fill="#f9e9ea" opacity="0.35" role="img" aria-label="Faint illustration of a tooth fairy flying beside a tooth"/>
      <rect class="illustration illustration--right" x="1440" y="840" width="330" height="540" rx="150" fill="#f7efe6" opacity="0.4" role="img" aria-label="Faint illustration of a tooth fairy holding a golden coin"/>

      <path class="wave wave--light" d="M0 1140 C 200 1700, 1000 1900, 1848 1830 L1848 2016 L0 2016 Z" fill="var(--sea-light)"/>
      <path class="wave wave--deep" d="M0 1262 C 260 1760, 1000 1930, 1848 1856 L1848 2016 L0 2016 Z" fill="var(--sea-deep)"/>
      <rect class="wave-strip" x="0" y="2003" width="1848" height="13" fill="var(--sea-light)"/>

      <rect class="page-frame" x="26" y="26" width="1796" height="1964" fill="none" stroke="var(--frame)" stroke-width="1.2"/>
    </svg>

    <header class="brand">
      <div class="brand__dot"></div>
      <h1 class="brand__name">Brindle Oaks Orthodontics</h1>
    </header>

    <address class="contact" style="font-style: normal;">
      <p class="contact__doctor">DOCTOR NAME</p>
      <p class="contact__line">123 Street Name</p>
      <p class="contact__line">City, State Zip code</p>
      <p class="contact__line">office@brindleoaksortho.com</p>
      <p class="contact__line">www.brindleoaksortho.com</p>
    </address>
  </main>
</body>
</html>
```